Website Design for Harbor Guidance

I am looking to create a website to help military members who are currently serving or have served to have a mentor. The military does an awful job and providing or offering a mentor program. People need someone they can come to with career advice with promotions, networking, building resumes, and pinging ideas off of on the occasion. I want a place where active and separated military members can come to, sign up and pick a program of offerings that make sense. They would register annually, pay for a membership package (can choose up to three) and then get support they need. Annual registration fees would be as follows and they would need to send payment through Paypal or other electronic means (credit card, eft, paypal, echeck, whatever).

I envision some type of registration that centers around the packages offered - this will be where the revision comes in once the framework is completed.

I am looking for very creative designs, and content, given the above, with verbiage around mentorship program. Please be creative for the design, and also put together three packages and price points for them three packages - put together what it would include in each package. We can modify as necessary during revisions. Final design should communicate military members in uniform with corporate leaders, something warm and inviting are important. I also want the abiity to really get this adversited and in the market for people to stumble across it easily.

I have purchased the domain already - harborguidance.com

Target Market(s)

Military, Veterans

Number of Pages Required

1 page

Requirements
Must have
• Military member with corporate look
• Modern and wide
• Warm and inviting
• Registration with ability to collect through PayPal, eCheck, Credit Card, etc)
• Creative design and content for the website based on what is described in the description
• About Section which has information about leadership team
• Contact Us
• Register
• 3 creative packages of what would be included (design this and the content keeping in mind the description)
• Content and the framework
• Some type of packages to consider (just examples but also needs mentoring options:
• https://www.careerdraftsmithy.com/
• https://www.cvbeacon.com/
• We are not going to ba resume writing service but we will offer it as part of our solution - I really want it to be focused around mentorship for job development, professional advice, interacting with peers, managers, leaders (using military acronyms like Supervisors and Leaders NCO's, Officers, etc)
• Blog so we can post topics and interact and respond to questions people have etc

```html
<!DOCTYPE html>
<html lang="en">
<head>
<meta charset="utf-8">
<title>Harbor Guidance — Mentorship for Service Members</title>
<link rel="stylesheet" href="https://fonts.googleapis.com/css2?family=Montserrat:wght@400;500;600;700;800&family=Open+Sans:wght@400;600;700&display=swap">
<style>
:root{
  --navy:#1b3a57;
  --navy-deep:#16324b;
  --band:#2c5275;
  --red:#b91c2c;
  --ink:#1e1e1e;
  --body:#3a3a3a;
  --grey-bg:#f2f2f2;
  --white:#ffffff;
  --line:#d9d9d9;
}
*{box-sizing:border-box;margin:0;padding:0}
html,body{width:1200px;height:3468px;overflow:hidden}
body{position:relative;background:var(--white);font-family:"Open Sans",Arial,sans-serif;color:var(--body)}
.abs{position:absolute}
.heading{font-family:"Montserrat",Arial,sans-serif;color:var(--ink)}

/* header */
.site-header{position:absolute;left:0;top:0;width:1200px;height:116px;background:var(--white)}
.brand{position:absolute;left:97px;top:34px;display:flex;align-items:center;gap:12px}
.brand-mark{width:26px;height:26px;background:var(--red)}
.brand-name{font-family:"Montserrat",Arial,sans-serif;font-weight:700;font-size:30px;color:var(--navy);letter-spacing:-.5px}
.signup{position:absolute;top:21px;height:34px;border-radius:3px;font-family:"Montserrat",Arial,sans-serif;font-size:14px;font-weight:500;display:flex;align-items:center;justify-content:center}
.signup.active{left:654px;width:208px;background:var(--navy);color:var(--white)}
.signup.military{left:881px;width:217px;border:1.5px solid var(--red);color:var(--red);background:var(--white)}
.main-nav{position:absolute;top:76px;left:414px;right:97px;display:flex;justify-content:space-between;font-family:"Montserrat",Arial,sans-serif;font-weight:600;font-size:15.5px;color:var(--ink)}

/* hero */
.hero{position:absolute;left:0;top:116px;width:1200px;height:584px;background:linear-gradient(180deg,#6d6a63 0%,#9c978c 40%,#7e7a73 70%,#5a5854 100%)}
.hero-person{position:absolute;right:0;top:0;width:560px;height:584px;background:linear-gradient(90deg,rgba(80,90,60,0) 0%,rgba(78,86,60,.55) 40%,rgba(70,78,55,.75) 100%)}
.hero-card{position:absolute;left:99px;top:289px;width:456px;height:273px;background:rgba(255,255,255,.93);border:3px solid rgba(200,200,200,.8);padding:30px 22px}
.hero-card h1{font-family:"Montserrat",Arial,sans-serif;font-weight:800;font-size:44px;color:var(--navy);letter-spacing:1px}
.hero-card p{font-family:"Montserrat",Arial,sans-serif;font-size:20px;line-height:29px;color:var(--navy);margin-top:8px}
.btn-red{display:inline-flex;align-items:center;justify-content:center;background:var(--red);color:var(--white);font-family:"Montserrat",Arial,sans-serif;font-weight:600;font-size:13px;border-radius:3px}
.hero-card .btn-red{margin-top:18px;width:115px;height:36px;font-size:14px}
.hero-arrow{position:absolute;top:260px}

/* feature band */
.feature-band{position:absolute;left:0;top:700px;width:1200px;height:248px;background:var(--band)}
.feature{position:absolute;top:642px;width:260px;text-align:center}
.feature-icon{width:136px;height:136px;margin:0 auto;border-radius:50%;background:var(--white);border:6px solid var(--navy-deep);display:flex;align-items:center;justify-content:center}
.feature h3{font-family:"Montserrat",Arial,sans-serif;font-weight:500;font-size:21px;color:var(--white);margin-top:18px}
.feature p{font-size:12.5px;line-height:23px;color:var(--white);margin-top:10px;padding:0 20px}

/* about */
.about-photo{position:absolute;left:122px;top:1010px;width:338px;height:338px;border-radius:50%;border:5px solid #8a8a8a;padding:10px;background:var(--white)}
.about-photo div{width:100%;height:100%;border-radius:50%;background:linear-gradient(90deg,#cfd6de 0%,#dfe3e8 49%,#6d6a55 51%,#9a9479 100%)}
.about-text{position:absolute;left:520px;top:1036px;width:560px}
.about-text h2{font-size:32px;font-weight:600}
.about-text p{font-size:12.5px;line-height:21px;color:var(--body);margin-top:18px}
.about-text .btn-red{margin-top:22px;width:109px;height:33px;font-size:11.5px}

/* pricing */
.pricing{position:absolute;left:0;top:1410px;width:1200px;height:636px;background:var(--grey-bg)}
.section-title{position:absolute;left:0;width:1200px;text-align:center;font-family:"Montserrat",Arial,sans-serif;font-weight:600;font-size:34px;color:var(--ink)}
.section-sub{position:absolute;left:300px;width:600px;text-align:center;font-size:12.5px;line-height:20px}
.price-card{position:absolute;top:1618px;width:284px;height:340px;background:var(--white);box-shadow:0 4px 14px rgba(0,0,0,.13);text-align:center;padding-top:24px}
.price-card h3{font-family:"Montserrat",Arial,sans-serif;font-weight:500;font-size:22px;color:var(--ink);margin-top:26px}
.price-card .tier{font-size:13px;color:var(--ink);margin-top:8px}
.price-card p{font-size:12px;line-height:21px;padding:0 40px;margin-top:12px}
.btn-outline{display:inline-flex;align-items:center;justify-content:center;width:114px;height:33px;border:1.5px solid var(--red);color:var(--red);font-family:"Montserrat",Arial,sans-serif;font-weight:600;font-size:11.5px;margin-top:16px}

/* offer */
.offer{position:absolute;top:2261px;width:180px;text-align:center}
.offer-icon{width:92px;height:92px;margin:0 auto;border-radius:50%;border:2.5px solid var(--navy);display:flex;align-items:center;justify-content:center}
.offer h4{font-family:"Montserrat",Arial,sans-serif;font-weight:500;font-size:19px;line-height:23px;color:var(--navy);margin-top:18px}

/* blog */
.title-rule{position:absolute;left:568px;top:2559px;width:64px;height:2px;background:var(--red)}
.blog-img{position:absolute}
.blog-title{position:absolute;font-family:"Montserrat",Arial,sans-serif;font-weight:600;font-size:17px;color:var(--navy)}
.blog-date{position:absolute;display:flex;align-items:center;gap:7px;font-family:"Montserrat",Arial,sans-serif;font-weight:600;font-size:13px;color:var(--red)}
.blog-text{position:absolute;font-size:12.5px;line-height:23px;color:var(--body)}

/* footer */
.site-footer{position:absolute;left:0;top:3087px;width:1200px;height:381px;background:var(--band);color:var(--white)}
.foot-h{position:absolute;top:69px;font-family:"Montserrat",Arial,sans-serif;font-weight:600;font-size:20px}
.quick-links{position:absolute;left:97px;top:112px;list-style:none;font-size:12.5px;line-height:22.5px}
.quick-links li::before{content:"›";margin-right:14px}
.contact-line{position:absolute;left:328px;display:flex;gap:14px;font-size:12.5px;line-height:21px}
.socials{position:absolute;left:332px;top:237px;display:flex;gap:6px}
.socials span{width:22px;height:22px;border-radius:50%;border:1.5px solid var(--white)}
.field{position:absolute;height:42px;border:1.5px solid rgba(255,255,255,.85);font-size:12px;padding:0 12px;display:flex;align-items:center}
.submit{position:absolute;left:633px;top:219px;width:222px;height:40px;background:var(--red);font-family:"Montserrat",Arial,sans-serif;font-weight:600;font-size:15px;display:flex;align-items:center;justify-content:center}
.foot-rule{position:absolute;left:0;top:316px;width:1200px;height:1px;background:rgba(255,255,255,.2)}
.copyright{position:absolute;left:0;top:340px;width:1200px;text-align:center;font-size:12.5px}
</style>
</head>
<body>

<header class="site-header">
  <div class="brand"><span class="brand-mark"></span><span class="brand-name">Harbor Guidance</span></div>
  <a class="signup active">Active Member Sign Up</a>
  <a class="signup military">Military Member Sign Up</a>
  <nav class="main-nav"><span>HOME</span><span>ABOUT US</span><span>WHAT WE OFFER</span><span>PACKAGES</span><span>BLOG</span><span>CONTACT US</span></nav>
</header>

<section class="hero" role="img" aria-label="Smiling service member in camouflage uniform holding a laptop in front of a city skyline">
  <div class="hero-person"></div>
  <svg class="hero-arrow" style="left:44px" width="20" height="40" viewBox="0 0 20 40"><path d="M17 3 3 20l14 17" fill="none" stroke="#fff" stroke-width="2"/></svg>
  <svg class="hero-arrow" style="left:1128px" width="20" height="40" viewBox="0 0 20 40"><path d="M3 3l14 17L3 37" fill="none" stroke="#fff" stroke-width="2"/></svg>
</section>
<div class="hero-card">
  <h1>HARBOR GUIDANCE</h1>
  <p>We provide career advice with promotions,<br>networking, building resumes</p>
  <a class="btn-red">REGISTER</a>
</div>

<div class="feature-band"></div>
<div class="feature" style="left:78px">
  <div class="feature-icon"><svg width="62" height="62" viewBox="0 0 24 24"><path d="M3 3h8l10 10-8 8L3 11z" fill="#b91c2c"/><circle cx="7.5" cy="7.5" r="1.6" fill="#fff"/></svg></div>
  <h3>Promotions</h3><p>Sed ut perspiciatis unde omnis iste natus error sit voluptatem accusa doloremque laudantium</p>
</div>
<div class="feature" style="left:332px">
  <div class="feature-icon"><svg width="62" height="62" viewBox="0 0 24 24" fill="#b91c2c"><rect x="9" y="3" width="6" height="5"/><rect x="2" y="16" width="6" height="5"/><rect x="9" y="16" width="6" height="5"/><rect x="16" y="16" width="6" height="5"/><path d="M11.3 8h1.4v3.3H19.7V16h-1.4v-3.3h-5.6V16h-1.4v-3.3H5.7V16H4.3v-4.7h7z"/></svg></div>
  <h3>Networking</h3><p>Sed ut perspiciatis unde omnis iste natus error sit voluptatem accusa doloremque laudantium</p>
</div>
<div class="feature" style="left:598px">
  <div class="feature-icon"><svg width="58" height="58" viewBox="0 0 24 24"><path d="M5 2h10l5 5v15H5z" fill="#b91c2c"/><path d="M15 2v5h5" fill="#e57380"/><path d="M8 11h9M8 14h9M8 17h6" stroke="#fff" stroke-width="1.3"/></svg></div>
  <h3>Building Resumes</h3><p>Sed ut perspiciatis unde omnis iste natus error sit voluptatem accusa doloremque laudantium</p>
</div>
<div class="feature" style="left:864px">
  <div class="feature-icon"><svg width="62" height="62" viewBox="0 0 24 24" fill="#b91c2c"><path d="M3 9h4l10-5v16L7 15H3z"/><path d="M6 15l2 6h3l-2-6z"/><path d="M19 9.5a3 3 0 0 1 0 5" stroke="#b91c2c" stroke-width="1.6" fill="none"/></svg></div>
  <h3>Pinging</h3><p>Sed ut perspiciatis unde omnis iste natus error sit voluptatem accusa doloremque laudantium</p>
</div>

<div class="about-photo" role="img" aria-label="Portrait split between a man in business shirt and tie and the same man in military uniform"><div></div></div>
<div class="about-text">
  <h2 class="heading">ABOUT HARBOR GUIDANCE</h2>
  <p>Sed ut perspiciatis unde omnis iste natus error sit voluptatem accusantium doloremque laudantium, totam rem aperiam, eaque ipsa quae ab illo inventore veritatis et quasi architecto beatae vitae dicta sunt explicabo. Nemo enim ipsam voluptatem quia voluptas sit aspernatur aut odit aut fugit, sed quia consequuntur magni dolores eos</p>
  <p>Lorem ipsum dolor sit amet, consectetur adipiscing elit, sed do eiusmod tempor incididunt ut labore et dolore magna aliqua. Ut enim ad minim veniam</p>
  <a class="btn-red">READ MORE</a>
</div>

<section class="pricing"></section>
<h2 class="section-title" style="top:1466px">OUR PRICING</h2>
<p class="section-sub" style="top:1526px">Nemo enim ipsam voluptatem quia voluptas sit aspernatur aut odit aut fugit, sed quia consequuntur magni dolores eos qui ratione voluptatem</p>

<div class="price-card" style="left:132px">
  <svg width="76" height="88" viewBox="0 0 30 36"><circle cx="15" cy="8" r="7" fill="#b91c2c"/><path d="M2 36v-9a9 9 0 0 1 9-9h8a9 9 0 0 1 9 9v9z" fill="#1b3a57"/><path d="M13 18h4l-1 3 2 10-3 3-3-3 2-10z" fill="#fff"/></svg>
  <h3>Professional – $190</h3><div class="tier">(years 2+)</div>
  <p>Sed ut perspiciatis unde omnis iste natus error sit voluptatem accusantium doloremque laudantium</p>
  <a class="btn-outline">GET STARTED</a>
</div>
<div class="price-card" style="left:458px">
  <svg width="88" height="88" viewBox="0 0 36 36"><rect x="2" y="3" width="32" height="23" fill="#1b3a57"/><rect x="5" y="6" width="26" height="17" fill="#fff"/><path d="M8 19l6-6 4 4 7-7" fill="none" stroke="#b91c2c" stroke-width="2"/><rect x="15" y="26" width="6" height="5" fill="#1b3a57"/><rect x="10" y="31" width="16" height="2.5" fill="#1b3a57"/></svg>
  <h3>Executive – $230</h3><div class="tier">(C-level executives, VPs)</div>
  <p>Sed ut perspiciatis unde omnis iste natus error sit voluptatem accusantium doloremque laudantium</p>
  <a class="btn-outline">GET STARTED</a>
</div>
<div class="price-card" style="left:784px">
  <svg width="88" height="88" viewBox="0 0 36 36"><rect x="12" y="4" width="12" height="6" fill="none" stroke="#b91c2c" stroke-width="2.4"/><rect x="2" y="9" width="32" height="11" fill="#b91c2c"/><rect x="2" y="21" width="32" height="12" fill="#1b3a57"/><rect x="15" y="18" width="6" height="5" fill="#fff"/></svg>
  <h3>Entry-Level – $150</h3><div class="tier">(to 1 year 0)</div>
  <p>Sed ut perspiciatis unde omnis iste natus error sit voluptatem accusantium doloremque laudantium</p>
  <a class="btn-outline">GET STARTED</a>
</div>

<h2 class="section-title" style="top:2102px">WHAT WE OFFER</h2>
<p class="section-sub" style="top:2172px;left:130px;width:940px;font-size:12.5px;line-height:22px">Sed ut perspiciatis unde omnis iste natus error sit voluptatem accusantium doloremque laudantium, totam rem aperiam, eaque ipsa quae ab illo inventore veritatis et quasi architecto beatae vitae dicta sunt explicabo. Nemo enim ipsam voluptatem</p>

<div class="offer" style="left:123px">
  <div class="offer-icon"><svg width="44" height="44" viewBox="0 0 24 24" fill="none" stroke="#1b3a57" stroke-width="1.6"><circle cx="12" cy="12" r="8"/><circle cx="12" cy="10" r="2.3" fill="#1b3a57"/><path d="M8 16a4 4 0 0 1 8 0"/><path d="M12 1v3M12 20v3M1 12h3M20 12h3"/></svg></div>
  <h4>Job<br>development</h4>
</div>
<div class="offer" style="left:312px">
  <div class="offer-icon"><svg width="44" height="44" viewBox="0 0 24 24" fill="none" stroke="#1b3a57" stroke-width="1.6"><circle cx="8" cy="6" r="2.5"/><circle cx="16" cy="6" r="2.5"/><path d="M3 15a5 5 0 0 1 10 0M11 15a5 5 0 0 1 10 0"/><rect x="3" y="15" width="18" height="3"/><path d="M6 18v4M18 18v4"/></svg></div>
  <h4>Professional<br>Advice</h4>
</div>
<div class="offer" style="left:516px">
  <div class="offer-icon"><svg width="46" height="46" viewBox="0 0 24 24" fill="none" stroke="#1b3a57" stroke-width="1.6"><path d="M2 10l4-4 4 2 4-2 4 2 4-2"/><path d="M6 14l4 4c1 1 2 1 3 0l5-5"/><path d="M9 11l3 3M11 9l3 3"/><path d="M2 10l4 4M22 8l-4 5"/></svg></div>
  <h4>Interacting with<br>Peers</h4>
</div>
<div class="offer" style="left:710px">
  <div class="offer-icon"><svg width="44" height="44" viewBox="0 0 24 24" fill="#1b3a57"><circle cx="12" cy="7" r="4.5"/><path d="M3 22a9 9 0 0 1 18 0z"/></svg></div>
  <h4>Managers</h4>
</div>
<div class="offer" style="left:893px">
  <div class="offer-icon"><svg width="48" height="48" viewBox="0 0 24 24" fill="#1b3a57"><circle cx="12" cy="7" r="3.2"/><circle cx="5.5" cy="9" r="2.5"/><circle cx="18.5" cy="9" r="2.5"/><path d="M6 19a6 6 0 0 1 12 0z"/><path d="M1 18a4.5 4.5 0 0 1 6-4.2A7 7 0 0 0 5 18zM23 18a4.5 4.5 0 0 0-6-4.2A7 7 0 0 1 19 18z"/></svg></div>
  <h4>Leaders NCO's</h4>
</div>

<h2 class="section-title" style="top:2495px">LATEST BLOG</h2>
<div class="title-rule"></div>

<div class="blog-img" style="left:113px;top:2617px;width:435px;height:227px;background:linear-gradient(135deg,#1d2c3f 0%,#35506b 55%,#1b2836 100%)" role="img" aria-label="Team of service members and civilians working together at computer screens"></div>
<div class="blog-title" style="left:113px;top:2865px">Nemo enim ipsam voluptatem quia voluptas</div>
<div class="blog-date" style="left:113px;top:2897px"><svg width="13" height="13" viewBox="0 0 12 12" fill="#b91c2c"><rect x="1" y="2" width="10" height="9" rx="1"/><rect x="2" y="5" width="8" height="5" fill="#fff"/></svg>JULY 05, 2018</div>
<p class="blog-text" style="left:113px;top:2926px;width:440px">Lorem ipsum dolor sit amet, consectetur adipiscing elit, sed do eiusmod tempor incididunt ut labore et dolore magna aliqua. Ut enim ad minim veniam</p>

<div class="blog-img" style="left:576px;top:2617px;width:173px;height:157px;background:linear-gradient(135deg,#6a6f63 0%,#9aa0a4 50%,#444a52 100%)" role="img" aria-label="Soldier working at a laptop"></div>
<div class="blog-title" style="left:770px;top:2620px">Nemo enim ipsam voluptatem</div>
<div class="blog-date" style="left:770px;top:2652px"><svg width="13" height="13" viewBox="0 0 12 12" fill="#b91c2c"><rect x="1" y="2" width="10" height="9" rx="1"/><rect x="2" y="5" width="8" height="5" fill="#fff"/></svg>JULY 05, 2018</div>
<p class="blog-text" style="left:770px;top:2681px;width:330px">Lorem ipsum dolor sit amet, consectetur adipiscing elit, sed do eiusmod tempor incididunt ut labore et dolore magna aliqua. Lorem ipsum dolor sit amet, consectetur adipiscing elit, sed do</p>

<div class="blog-img" style="left:576px;top:2823px;width:173px;height:173px;background:linear-gradient(135deg,#111 0%,#3d3d3d 55%,#0c0c0c 100%)" role="img" aria-label="Hands typing on a keyboard in front of a monitor"></div>
<div class="blog-title" style="left:770px;top:2825px">Nemo enim ipsam voluptatem</div>
<div class="blog-date" style="left:770px;top:2857px"><svg width="13" height="13" viewBox="0 0 12 12" fill="#b91c2c"><rect x="1" y="2" width="10" height="9" rx="1"/><rect x="2" y="5" width="8" height="5" fill="#fff"/></svg>JULY 05, 2018</div>
<p class="blog-text" style="left:770px;top:2886px;width:330px">Lorem ipsum dolor sit amet, consectetur adipiscing elit, sed do eiusmod tempor incididunt ut labore et dolore magna aliqua. Lorem ipsum dolor sit amet, consectetur adipiscing elit, sed do</p>

<footer class="site-footer">
  <h3 class="foot-h" style="left:97px">QUICK LINK</h3>
  <h3 class="foot-h" style="left:328px">CONTACT US</h3>
  <h3 class="foot-h" style="left:631px">GET A QUOTE</h3>
  <ul class="quick-links"><li>Home</li><li>About Us</li><li>Services</li><li>Blog</li><li>Testimonials</li><li>Contact Us</li></ul>
  <div class="contact-line" style="top:112px"><svg width="14" height="18" viewBox="0 0 12 16" fill="#fff"><path d="M6 0a6 6 0 0 1 6 6c0 4-6 10-6 10S0 10 0 6a6 6 0 0 1 6-6z"/><circle cx="6" cy="6" r="2" fill="#2c5275"/></svg><span>Harbor Guidance 4820 Anchor Street<br>Suite 206 Bayview, FL 33010</span></div>
  <div class="contact-line" style="top:165px"><svg width="15" height="15" viewBox="0 0 24 24" fill="#fff"><path d="M6.6 10.8a15 15 0 0 0 6.6 6.6l2.2-2.2c.3-.3.7-.4 1-.2 1.1.4 2.3.6 3.6.6.6 0 1 .4 1 1V20c0 .6-.4 1-1 1A17 17 0 0 1 3 4c0-.6.4-1 1-1h3.5c.6 0 1 .4 1 1 0 1.3.2 2.5.6 3.6.1.3 0 .7-.2 1z"/></svg><span>Phone: +1 555-014-2290</span></div>
  <div class="contact-line" style="top:197px"><svg width="15" height="15" viewBox="0 0 24 24" fill="#fff"><path d="M2 5h20v14H2z"/><path d="M2 5l10 8 10-8" stroke="#2c5275" stroke-width="2" fill="none"/></svg><span>info@harborguidance.com</span></div>
  <div class="socials"><span></span><span></span><span></span><span></span></div>
  <div class="field" style="left:633px;top:108px;width:222px">Your Name</div>
  <div class="field" style="left:872px;top:108px;width:228px">Your E - Mail</div>
  <div class="field" style="left:633px;top:159px;width:222px">Your Phone</div>
  <div class="field" style="left:872px;top:159px;width:228px">Message</div>
  <div class="submit">SUBMIT</div>
  <div class="foot-rule"></div>
  <p class="copyright">©2018 Harbor Guidance, All Rights Reserved.</p>
</footer>

</body>
</html>
```